Business Card for Multi-Brand Sportswear Company

We are looking for a business card which represents our company and the multiple brands within it.

The company: Fen Athletics (LTD)
The brands: Fen, TavaPuni, ElmStretch, Grit and Rain

Employees using these cards would be representing Fen Athletics, rather than any of the individual brands. You will see a current design within the uploaded files, to give some inspiration. The actual text of the brands is not necessary, but the logos should be on there is some format.

Our creative minds on this are stretched, so we are looking for someone to make this their own, and show us what a good business card should look like.

We may like to get these printed with spot gloss, so keep that in mind with your designs.

www.fenathletics.co.uk

Industry/Entity Type

Business

Contact Information for Business Card

Leo Pemberton-Hale
Operations Manager
(+44) 1632 960 418
Leo@fenathletics.co.uk
www.fenathletics.co.uk

Font styles to use
Sans Serif
Other font styles liked:
• Eurostile

Colors
ffffff

Requirements
Nice to have
• Dark (black) background

```html
<!DOCTYPE html>
<html lang="en">
<head>
<meta charset="utf-8">
<title>Fen Athletics – Business Card</title>
<link rel="stylesheet" href="https://fonts.googleapis.com/css2?family=Saira:wght@400;600;800&display=swap">
<style>
  :root {
    --page: #2a2a2c;
    --card: #0b0b0c;
    --card-edge: #161618;
    --red: #e3232b;
    --white: #ffffff;
    --silver: #c9c9cc;
    --grey: #8d8d92;
    --chip: #5d5566;
  }
  * { box-sizing: border-box; margin: 0; padding: 0; }
  html, body { width: 1200px; height: 900px; overflow: hidden; }
  body {
    background: var(--page);
    font-family: "Saira", "Helvetica Neue", Arial, sans-serif;
    position: relative;
  }
  .card {
    position: absolute;
    width: 560px;
    height: 320px;
    background: linear-gradient(160deg, var(--card-edge), var(--card) 60%);
    overflow: hidden;
    box-shadow: 0 18px 40px rgba(0,0,0,.55);
  }
  .card svg.shapes { position: absolute; inset: 0; }
  .card--front { left: 60px; top: 110px; }
  .card--back { left: 580px; top: 470px; }

  .wordmark {
    position: absolute;
    font-weight: 600;
    color: var(--silver);
    letter-spacing: 1px;
    white-space: nowrap;
  }
  .card--front .wordmark { left: 90px; top: 92px; font-size: 44px; }
  .tagline {
    position: absolute;
    left: 290px; top: 150px;
    font-size: 11px;
    letter-spacing: 3px;
    color: var(--grey);
  }
  .card--back .wordmark { left: 36px; top: 38px; font-size: 36px; }

  .identity {
    position: absolute;
    right: 28px; top: 108px;
    text-align: right;
    color: var(--white);
    line-height: 1.15;
  }
  .identity .name { font-weight: 800; font-size: 19px; }
  .identity .role { color: var(--red); font-size: 15px; }
  .identity .address { font-size: 14px; }

  .divider {
    position: absolute;
    left: 30px; top: 196px;
    width: 340px; height: 1.5px;
    background: var(--red);
  }

  .brands {
    position: absolute;
    left: 30px; top: 168px;
    display: flex; gap: 14px; align-items: center;
  }
  .brand {
    font-size: 11px; font-weight: 600;
    color: var(--red);
    display: flex; align-items: center; gap: 5px;
  }
  .brand::before {
    content: ""; width: 8px; height: 8px;
    background: var(--chip);
  }

  .contacts {
    position: absolute;
    left: 34px; top: 208px;
    list-style: none;
    color: var(--white);
    font-size: 15px;
    line-height: 1.35;
  }
  .contacts li { display: flex; align-items: center; gap: 8px; }
  .contacts svg { width: 12px; height: 12px; flex: none; }
</style>
</head>
<body>

<section class="card card--front" aria-label="Card front">
  <svg class="shapes" viewBox="0 0 560 320" aria-hidden="true">
    <polygon points="0,262 262,262 560,176 560,194 272,286 0,286" fill="var(--white)"/>
    <polygon points="266,256 296,246 306,250 276,260" fill="var(--red)"/>
    <polygon points="300,245 326,237 336,241 310,249" fill="var(--red)"/>
    <polygon points="330,236 356,228 366,232 340,240" fill="var(--red)"/>
  </svg>
  <div class="wordmark">Fen Athletics</div>
  <div class="tagline">PERFORMANCE WEAR</div>
</section>

<section class="card card--back" aria-label="Card back">
  <svg class="shapes" viewBox="0 0 560 320" aria-hidden="true">
    <polygon points="0,300 330,252 326,272 0,320" fill="var(--red)"/>
    <polygon points="338,250 352,248 348,268 334,270" fill="var(--white)"/>
    <polygon points="356,247 378,244 374,264 352,267" fill="var(--white)"/>
    <polygon points="382,243 404,240 400,260 378,263" fill="var(--white)"/>
    <polygon points="404,270 418,226 560,204 560,258" fill="var(--red)"/>
  </svg>

  <div class="wordmark">Fen Athletics</div>

  <div class="identity">
    <div class="name">Leo Pemberton-Hale</div>
    <div class="role">Operations Manager</div>
    <div class="address">Marsh Lane, Oakby<br>Ripton, YO9 4PX</div>
  </div>

  <div class="brands">
    <span class="brand">TavaPuni</span>
    <span class="brand">Grit and Rain</span>
    <span class="brand">ElmStretch</span>
  </div>

  <div class="divider"></div>

  <ul class="contacts">
    <li>
      <svg viewBox="0 0 12 12" aria-hidden="true"><circle cx="6" cy="6" r="6" fill="var(--red)"/><path d="M4 3.2l1 1.3-.6.7c.4.9 1 1.5 1.9 1.9l.7-.6 1.3 1-.6 1.1C5.7 8.5 3.5 6.3 3.3 3.8z" fill="var(--white)"/></svg>
      (+44) 1632 960 418
    </li>
    <li>
      <svg viewBox="0 0 12 12" aria-hidden="true"><circle cx="6" cy="6" r="6" fill="var(--red)"/><rect x="3" y="4" width="6" height="4.2" fill="none" stroke="var(--white)" stroke-width=".9"/><path d="M3 4l3 2.3L9 4" fill="none" stroke="var(--white)" stroke-width=".9"/></svg>
      Leo@fenathletics.co.uk
    </li>
    <li>
      <svg viewBox="0 0 12 12" aria-hidden="true"><circle cx="6" cy="6" r="6" fill="var(--red)"/><circle cx="6" cy="6" r="3" fill="none" stroke="var(--white)" stroke-width=".8"/><path d="M3 6h6M6 3c-1.4 1.6-1.4 4.4 0 6M6 3c1.4 1.6 1.4 4.4 0 6" fill="none" stroke="var(--white)" stroke-width=".7"/></svg>
      www.fenathletics.co.uk
    </li>
  </ul>
</section>

</body>
</html>
```